Business Card - Tidal Lanes

Need Business Card design for company named Tidal Lanes. Software development focused mainly on Brindle Orvix & Zelt Apps. I've attached our logo with both a black and white background. Please add trademark symbol to logo when using.

```html
<!DOCTYPE html>
<html lang="en">
<head>
<meta charset="utf-8">
<title>Tidal Lanes Business Card</title>
<link rel="stylesheet" href="https://fonts.googleapis.com/css2?family=Open+Sans:wght@400;600;700&display=swap">
<style>
  :root {
    --bg: #e6e7ec;
    --card-black: #000000;
    --orange: #ff9a33;
    --red: #d7171b;
    --yellow: #f5b800;
    --white: #ffffff;
  }
  * { margin: 0; padding: 0; box-sizing: border-box; }
  html, body {
    width: 1200px; height: 987px; overflow: hidden;
    background: var(--bg);
    font-family: "Open Sans", sans-serif;
  }
  .stage { position: relative; width: 1200px; height: 987px; }
  .card {
    position: absolute; left: 250px; width: 700px; height: 400px;
    border-radius: 28px; overflow: hidden; background: var(--card-black);
    box-shadow: 0 8px 24px rgba(0,0,0,0.18);
  }
  .card--back { top: 60px; }
  .card--front { top: 527px; }

  .brand {
    display: flex; align-items: center; gap: 14px;
    color: var(--white); font-weight: 700; letter-spacing: -1px;
  }
  .brand__dot { width: 22px; height: 22px; border-radius: 50%; background: var(--orange); }
  .brand__tm { font-size: 14px; font-weight: 700; align-self: flex-end; margin-bottom: 6px; letter-spacing: 0; }

  .card--back .brand { position: absolute; top: 130px; left: 0; right: 0; justify-content: center; font-size: 54px; }
  .website {
    position: absolute; top: 236px; left: 0; right: 0; text-align: center;
    color: var(--white); font-size: 24px; letter-spacing: 3px;
  }

  .front-art { position: absolute; inset: 0; }
  .card--front .brand { position: absolute; top: 66px; left: 44px; font-size: 46px; }
  .person { position: absolute; top: 100px; right: 60px; text-align: right; }
  .person__name { color: var(--yellow); font-weight: 700; font-size: 26px; }
  .person__title { color: var(--white); font-size: 22px; margin-top: 2px; }

  .contact {
    position: absolute; bottom: 26px; right: 48px; text-align: right;
    color: var(--white); font-size: 22px; line-height: 1.45;
  }
  .contact__line { display: flex; align-items: center; justify-content: flex-end; gap: 10px; }
  .contact__icon { width: 20px; height: 20px; fill: var(--white); }
</style>
</head>
<body>
<main class="stage">
  <section class="card card--back">
    <div class="brand">
      <span class="brand__dot"></span>
      <span class="brand__name">Tidal Lanes</span>
      <span class="brand__tm">™</span>
    </div>
    <p class="website">www.tidallanes.com</p>
  </section>

  <section class="card card--front">
    <svg class="front-art" viewBox="0 0 700 400" width="700" height="400" aria-hidden="true">
      <path d="M0 205 C 180 250, 330 305, 470 300 C 560 296, 640 270, 700 240 L700 400 L0 400 Z" fill="var(--orange)"/>
      <path d="M0 170 C 140 230, 300 285, 455 296 C 320 300, 150 250, 0 198 Z" fill="var(--red)"/>
    </svg>
    <div class="brand">
      <span class="brand__dot"></span>
      <span class="brand__name">Tidal Lanes</span>
      <span class="brand__tm">™</span>
    </div>
    <div class="person">
      <p class="person__name">Your Name</p>
      <p class="person__title">Title</p>
    </div>
    <div class="contact">
      <p class="contact__line">
        <svg class="contact__icon" viewBox="0 0 20 20" aria-hidden="true"><rect x="5" y="1" width="10" height="18" rx="2"/><rect x="7" y="4" width="6" height="7" fill="var(--orange)"/></svg>
        555-214-7780
      </p>
      <p class="contact__line">
        <svg class="contact__icon" viewBox="0 0 20 20" aria-hidden="true"><path d="M2 7 Q10 1 18 7 L16 9 L13 8 L13 6 Q10 5 7 6 L7 8 L4 9 Z"/><rect x="3" y="11" width="14" height="7" rx="2"/></svg>
        555-390-4416
      </p>
      <p class="contact__line">2410 Harbor Row, Bayfield, FL 30921</p>
    </div>
  </section>
</main>
</body>
</html>
```